Non Profit Company Looking For New Website

The website for Fernvale Quillstone Heritage Society should offer the viewer beautiful photos that inspire condifence and joy and tap into our love of horses.

We would like to see a website that displays trust, quality and confidence. Needs to be responsive and mobile friendly for all browsers and coded for both Android & IOS.

READ ATTACHED WEBSITE TEMPLATE FOR COMPLETE DETAILS ON WHAT WE ARE LOOKING FOR.

Looking for recommmendations if we should use WordPress/WooCommerce for site or Wordpress with Shopify Plug in or just Shopify.

Must be both desktop and mobile friendly with fast page load speed. Need the ability to edit ourselves.

Industry/Entity Type

Non Profit

Coding

Coded - Design and coding required

Number of Pages Required

5+ page

Requirements
Must have
• We would like to see a website that displays trust, quality and confidence. Needs to be responsive and mobile friendly for all browsers and coded for both Android & IOS.

Looking for recommendations if we should use WordPress/WooCommerce for site or Wordpress with Shopify Plug in or just Shopify.

Logo Colour:
Pantone 7621 C

READ TEMPLATE THAT IS ATTACHED
Nice to have
• Like look of this website as a sample:
https://www.quellbrimtorva.com/

Another similar non profit organization
https://pellaworthcindle.com/

```html
<!DOCTYPE html>
<html lang="en">
<head>
<meta charset="utf-8">
<title>Fernvale Quillstone Heritage Society</title>
<link rel="stylesheet" href="https://fonts.googleapis.com/css2?family=Cinzel:wght@400;500&family=Roboto:wght@400;500;700&display=swap">
<style>
:root{
  --red:#9b1020;
  --ink:#1c1c1c;
  --hero-bg:#e9e1dc;
  --pink:#f1d3d8;
  --black:#0a0a0a;
  --white:#fff;
  --line:#b9b9b9;
}
*{box-sizing:border-box;margin:0;padding:0}
html,body{width:1200px;height:3838px;overflow:hidden}
body{position:relative;background:var(--white);font-family:"Roboto",sans-serif;color:var(--ink)}
.abs{position:absolute;z-index:2}
.serif{font-family:"Cinzel",serif;color:var(--red);font-weight:500}
.btn{position:absolute;z-index:2;display:flex;align-items:center;justify-content:center;border:2px solid var(--red);border-radius:3px;color:var(--red);font-size:19px;text-decoration:none;background:transparent}
.photo{position:absolute}

/* hero */
.hero{position:absolute;z-index:1;left:0;top:0;width:1200px;height:790px;overflow:hidden;background:var(--hero-bg)}
.hero-photo{left:640px;top:0;width:560px;height:760px;
  background:
    linear-gradient(180deg,rgba(233,225,220,.95) 0,rgba(233,225,220,.7) 70px,rgba(233,225,220,0) 160px),
    linear-gradient(90deg,rgba(233,225,220,1) 0%,rgba(233,225,220,.6) 14%,rgba(233,225,220,0) 32%),
    radial-gradient(ellipse at 55% 50%,#b07a52 0%,#8a5a3e 35%,#5a3e36 60%,#cdbba9 100%)}
.brand{position:absolute;z-index:2;left:140px;top:14px;width:170px;text-align:center;font-family:"Cinzel",serif;color:var(--red);font-weight:500;line-height:1.1}
.brand .l1{font-size:27px}
.brand .mark{width:40px;height:40px;border-radius:50%;background:var(--red);margin:10px auto 12px}
.brand .l2{font-size:17px}
.nav{position:absolute;z-index:2;top:38px;left:522px;display:flex;gap:34px;font-size:16px;font-weight:500;color:#1a1a1a}
.nav a{color:inherit;text-decoration:none;padding-bottom:8px}
.nav a.active{color:var(--red);border-bottom:3px solid var(--red)}
.hero-lead{left:143px;top:236px;font-size:30px;line-height:37px;font-weight:500;width:460px}
.hero-tag{left:143px;top:372px;font-size:36px;letter-spacing:0;white-space:nowrap}
.hero-body{left:143px;top:440px;font-size:21px;line-height:30px}
.dots{left:143px;top:668px;display:flex;gap:10px}
.dots span{width:10px;height:10px;border-radius:50%;background:#aaa}
.dots span.on{background:var(--red)}

/* about */
.mini-mark{left:582px;top:795px;width:36px;height:36px;border-radius:50%;background:var(--red)}
.about-title{left:0;width:1200px;top:890px;text-align:center;font-size:38px}
.about-text{left:180px;width:840px;top:965px;text-align:center;font-size:14px;line-height:30px;color:#444}

/* adopt */
.adopt-title{left:0;width:1200px;top:1340px;text-align:center;font-size:40px;color:var(--white)}
.adopt-sub{left:0;width:1200px;top:1413px;text-align:center;font-size:18px;color:var(--white);font-weight:500}
.horse{position:absolute;z-index:2;width:296px;height:270px}
.horse-info{position:absolute;left:0;bottom:0;width:100%;height:150px;background:linear-gradient(transparent,rgba(0,0,0,.85));color:#fff;padding:0 26px}
.horse-info h3{font-size:15px;font-weight:500;margin-top:12px}
.horse-info p{font-size:10px;margin-top:10px;line-height:14px}
.horse-info .mini{display:inline-block;border:1px solid #fff;border-radius:2px;font-size:7px;padding:7px 16px;margin:14px 6px 0 0}

/* give */
.give{position:absolute;z-index:1;left:0;top:2250px;width:1200px;height:650px;background:var(--pink);overflow:hidden}
.give-photo{left:0;top:0;width:760px;height:650px;background:linear-gradient(90deg,#4a3a3e 0%,#6e5a5e 45%,#a98a90 70%,rgba(241,211,216,0) 92%)}
.give-title{left:660px;top:2420px;font-size:40px}
.give-text{left:660px;top:2493px;width:450px;font-size:15px;line-height:30px;color:#444}

/* contact */
.contact-title{left:0;width:1200px;top:2990px;text-align:center;font-size:40px;line-height:46px}
.info{position:absolute;z-index:2;left:148px;display:flex;align-items:center;gap:14px;font-size:15px;line-height:21px;color:#333}
.info .ic{width:54px;height:54px;border:2px solid var(--red);border-radius:50%;display:flex;align-items:center;justify-content:center}
.field{position:absolute;z-index:2;border:1px solid var(--line);font-size:12px;color:#555;padding:20px 24px}
.captcha{position:absolute;z-index:2;left:568px;top:3400px;width:256px;height:66px;border:1px solid #d3d3d3;background:#f9f9f9;box-shadow:0 0 3px rgba(0,0,0,.08);display:flex;align-items:center;padding:0 14px;gap:12px;font-size:12px}
.captcha .box{width:24px;height:24px;border:2px solid #c1c1c1;border-radius:2px;background:#fff}
.captcha .badge{margin-left:auto;width:30px;height:30px;border-radius:4px;background:#c7d4ea}

/* footer */
.foot-brand{left:810px;top:3605px;width:260px;text-align:center;font-family:"Cinzel",serif;color:var(--red);font-weight:500;line-height:1.1}
.foot-brand .l1{font-size:40px}
.foot-brand .mark{width:56px;height:56px;border-radius:50%;background:var(--red);margin:16px auto}
.foot-brand .l2{font-size:25px}
.social{left:145px;top:3690px;display:flex;gap:14px}
.social span{width:20px;height:20px;border-radius:50%;background:var(--white)}
.foot-nav{left:145px;top:3740px;font-size:19px;font-weight:700;color:var(--white);word-spacing:4px}
.foot-nav i{font-style:normal;margin:0 10px}
.copy{left:145px;top:3792px;font-size:12px;color:#ddd}
</style>
</head>
<body>

<section class="hero">
  <div class="photo hero-photo" role="img" aria-label="Young woman smiling and resting her head against a chestnut horse with a white blaze"></div>
  <svg class="abs" style="left:0;top:0" width="1200" height="790" viewBox="0 0 1200 790">
    <path d="M0 730 C 220 800 420 790 700 720 C 900 670 1050 680 1200 730 L1200 790 L0 790 Z" fill="#fff"/>
    <path d="M0 730 C 220 800 420 790 700 720 C 900 670 1050 680 1200 735" fill="none" stroke="var(--red)" stroke-width="5"/>
  </svg>
</section>

<div class="brand"><div class="l1">Fernvale</div><div class="mark"></div><div class="l2">Quillstone<br>Heritage</div></div>
<nav class="nav"><a class="active">HOME</a><a>ABOUT</a><a>ADOPT</a><a>HORSES</a><a>DONATE</a><a>CONTACT</a></nav>

<p class="abs hero-lead">We support and develop retired Thoroughbred racehorses for their next chapter in life</p>
<h1 class="abs serif hero-tag">RETIRE. RETRAIN. REHOME.</h1>
<p class="abs hero-body">Fernvale Quillstone Heritage Society (FQHS)<br>is a registered not-for-profit organization in Fernvale.</p>
<a class="btn" style="left:143px;top:535px;width:265px;height:69px">VIEW OUR HORSES</a>
<div class="abs dots"><span></span><span></span><span class="on"></span><span></span><span></span></div>

<div class="abs mini-mark"></div>
<h2 class="abs serif about-title">WHAT IS THOROUGHBRED AFTERCARE?</h2>
<p class="abs about-text">The health, safety and welfare of our equine athletes does not end at the finish line, and retirement and aftercare are critical to the success of the racing industry.Aftercare is the safe placement of racehorses after their careers as racehorse are completed. Some horses might retire to the breeding shed or broodmare bands, while others are retrained for second careers.</p>
<a class="btn" style="left:467px;top:1098px;width:266px;height:68px">LEARN MORE ABOUT US</a>

<svg class="abs" style="left:0;top:1245px;z-index:1" width="1200" height="440" viewBox="0 0 1200 440">
  <path d="M0 0 H1200 V330 C 1000 360 850 420 600 410 C 350 400 150 380 0 390 Z" fill="var(--red)"/>
</svg>
<h2 class="abs serif adopt-title">ADOPT A HORSE</h2>
<p class="abs adopt-sub">Fernvale Quillstone Heritage is committed to helping match you with the perfect horse.</p>

<div class="horse" style="left:144px;top:1498px;background:linear-gradient(135deg,#3c2a14,#b0602a 50%,#e2a05c)" role="img" aria-label="Chestnut horse with white blaze in warm evening light"></div>
<div class="horse" style="left:452px;top:1498px;background:linear-gradient(180deg,#5f6a2c,#6a3a24 55%,#1a1a1a)" role="img" aria-label="Bay horse galloping through a green field">
  <div class="horse-info"><h3>LOREM IPSUM DOLO</h3><p>Birth Year &nbsp;&nbsp;2018 &nbsp;Color Bay<br>Gender &nbsp;&nbsp;&nbsp;&nbsp;&nbsp;&nbsp;Gelding &nbsp;&nbsp;&nbsp;&nbsp;Location &nbsp;&nbsp;&nbsp;LEXINGTON, KY</p><span class="mini">LEARN MORE</span><span class="mini">ADOPT NOW</span></div>
</div>
<div class="horse" style="left:760px;top:1498px;background:linear-gradient(135deg,#a2593a,#4a2416 55%,#8a4a30)" role="img" aria-label="Dark bay horse in halter against autumn trees"></div>
<div class="horse" style="left:144px;top:1780px;background:linear-gradient(135deg,#5e7c93,#7a4a2c 45%,#c9a07a)" role="img" aria-label="Shaggy chestnut pony with long mane by a snowy hill"></div>
<div class="horse" style="left:452px;top:1780px;background:linear-gradient(180deg,#6e6a86,#b9a9a8 55%,#d2c3b4)" role="img" aria-label="Bay horse galloping across sand under a dusk sky"></div>
<div class="horse" style="left:760px;top:1780px;background:linear-gradient(135deg,#3a4a3a,#1d1c1a 50%,#4a5a42)" role="img" aria-label="Black horse with white stripe in front of green forest"></div>
<a class="btn" style="left:467px;top:2112px;width:266px;height:68px">ADOPT NOW</a>

<section class="give">
  <div class="photo give-photo" role="img" aria-label="Rider in helmet hugging a bridled horse, tinted in soft rose"></div>
</section>
<h2 class="abs serif give-title">MAKE A DIFFERENCE</h2>
<p class="abs give-text">Lorem ipsum dolor sit amet, consectetur adipiscing elit, sed do eiusmod tempor incididunt ut labore et dolore magna alinim minim veniam, quis nostrud exercitation ullamco laboris nisi ut aliquip ex ea commodo consequat. Duis aute irure dolor in reprehenderit</p>
<a class="btn" style="left:658px;top:2628px;width:266px;height:68px">MORE WAYS TO GIVE</a>

<h2 class="abs serif contact-title">HAVE A QUESTION OR NEED<br>MORE INFORMATION</h2>

<div class="info" style="top:3168px"><span class="ic"><svg width="18" height="24" viewBox="0 0 18 24"><path d="M9 1a8 8 0 0 0-8 8c0 6 8 14 8 14s8-8 8-14a8 8 0 0 0-8-8z" fill="var(--red)"/><circle cx="9" cy="9" r="3" fill="#fff"/></svg></span><span>234,Lorem ipsum dolor simet<br>consectetur isciusmod</span></div>
<div class="info" style="top:3243px"><span class="ic"><svg width="22" height="22" viewBox="0 0 24 24"><path d="M6.6 10.8a15 15 0 0 0 6.6 6.6l2.2-2.2a1 1 0 0 1 1-.25 11.4 11.4 0 0 0 3.6.6 1 1 0 0 1 1 1V20a1 1 0 0 1-1 1A17 17 0 0 1 3 4a1 1 0 0 1 1-1h3.5a1 1 0 0 1 1 1c0 1.25.2 2.45.6 3.6a1 1 0 0 1-.25 1z" fill="var(--red)"/></svg></span><span>Phone<br>1 888 888 8888</span></div>
<div class="info" style="top:3318px"><span class="ic"><svg width="24" height="18" viewBox="0 0 24 18"><rect x="0" y="0" width="24" height="18" rx="2" fill="var(--red)"/><path d="M1 2l11 8 11-8" fill="none" stroke="#fff" stroke-width="2"/></svg></span><span>Email<br>info@fernvalequillstone.org</span></div>

<div class="field" style="left:567px;top:3170px;width:236px;height:54px">First Name</div>
<div class="field" style="left:814px;top:3170px;width:236px;height:54px">Last Name</div>
<div class="field" style="left:567px;top:3238px;width:236px;height:54px">Enter Email</div>
<div class="field" style="left:814px;top:3238px;width:236px;height:54px">Phone</div>
<div class="field" style="left:567px;top:3306px;width:483px;height:78px">Message</div>
<div class="captcha"><span class="box"></span><span>I'm not a robot</span><span class="badge"></span></div>
<a class="btn" style="left:898px;top:3400px;width:152px;height:68px">SUBMIT</a>

<svg class="abs" style="left:0;top:3530px;z-index:1" width="1200" height="308" viewBox="0 0 1200 308">
  <path d="M0 60 C 300 110 600 100 900 40 C 1020 15 1120 20 1200 40 V308 H0 Z" fill="var(--black)"/>
  <path d="M0 60 C 300 110 600 100 900 40 C 1020 15 1120 20 1200 40" fill="none" stroke="var(--red)" stroke-width="5"/>
</svg>
<div class="abs foot-brand"><div class="l1">Fernvale</div><div class="mark"></div><div class="l2">Quillstone<br>Heritage</div></div>
<div class="abs social"><span></span><span></span><span></span></div>
<div class="abs foot-nav">HOME<i>/</i>ABOUT<i>/</i>ADOPT<i>/</i>HORSES<i>/</i>DONATE<i>/</i>CONTACT</div>
<p class="abs copy">© 2021 Fernvale Quillstone Heritage.All Rights reserved | Privacy Policy</p>

</body>
</html>
```